Vorelan.com Personal Trainer/Fitness Website

I want a website to market my personal training/Outdoor Bootcamp Class services, as well as to ditribute nutrivex. I need a logo as well I included an address for the Harbor Gales 1975 logo. I'd like Vorelan in place of Harbor Gales, and in Black and white, just different enough so I can't get sued by the PBL.
https://www.pictofind.example/imgres?imgurl=http%3A%2F%2Fwww.darnell-quibury.example%2Fwp-content%2Fuploads%2F2014%2F01%2Fgales_logo4.jpg&imgrefurl=http%3A%2F%2Fwww.darnell-quibury.example%2Fpbl-logo-redesigns-harbor-gales%2F&docid=_qkwzR7TBAgXpL&tbnid=m4tpU8KdOXjnRP%3A&w=600&h=450&client=ms-android-carrier&bih=512&biw=360&ved=0ahUKEwiRtpgyp9HMAhUTwGMKHRPMBWMQMwg6KBQwFA&iact=mrc&uact=8.
It should be about 5 pages 1. home 2. about 3. Services 4. Blog/Videos and programs 5. Contact.
http://www.dorvinfitness.example.uk/ is a website I like the style of.

Target Market(s)

Seattle area

Industry/Entity Type

Fitness

Coding

Coded - Design and coding required

Number of Pages Required

4 page

Font styles to use
Serif
Sans Serif

Requirements
Must have
• A minimal look
Nice to have
• A logo similar to the 1975 Harbor Galewinds Logo, with a Small Milo Brandt ripping his shirt open(with a picture of the logo on his shirt, picture within picture) to turn into Ironjaw in the center. Skyline is black, Background and small figure white(with black logo on shirt)

```html
<!DOCTYPE html>
<html lang="en">
<head>
<meta charset="utf-8">
<title>Vorelan — Personal &amp; Group Training</title>
<link href="https://fonts.googleapis.com/css2?family=Montserrat:wght@400;600;700;800&family=Open+Sans:wght@400;600;700&display=swap" rel="stylesheet">
<style>
:root{
  --green:#0c6a36;
  --green-dark:#08552a;
  --green-light:#1f8a4c;
  --yellow:#f7bd17;
  --gray:#5d5d5f;
  --gray-dark:#3f3f41;
  --black:#0d0d0d;
  --footer:#2b2b2b;
  --white:#ffffff;
  --ink:#2a2a2a;
}
*{box-sizing:border-box;margin:0;padding:0}
html,body{width:1200px;height:3462px;overflow:hidden}
body{position:relative;background:var(--white);font-family:"Open Sans",Arial,sans-serif;color:var(--ink)}
.abs{position:absolute}
section,header,nav,footer{position:absolute;left:0;width:1200px}

/* header */
.site-header{top:0;height:134px;background:var(--white)}
.brand{left:80px;top:30px;display:flex;align-items:center;gap:12px}
.brand-dot{width:26px;height:26px;border-radius:50%;background:var(--green)}
.brand-name{font-family:"Montserrat",sans-serif;font-weight:800;font-size:34px;color:var(--green);letter-spacing:1px}
.join-btn{left:905px;top:23px;width:215px;height:42px;background:var(--green);color:var(--white);font-family:"Montserrat",sans-serif;font-weight:600;font-size:20px;display:flex;align-items:center;justify-content:center;border-radius:3px}
.header-contact{left:852px;top:82px;display:flex;align-items:center;gap:10px;font-family:"Montserrat",sans-serif;font-weight:700;font-size:21px;color:var(--ink)}
.round-icon{width:30px;height:30px;border-radius:50%;background:var(--green);display:flex;align-items:center;justify-content:center;flex-shrink:0}
.social{width:28px;height:28px;border-radius:50%;flex-shrink:0}

/* nav */
.main-nav{top:134px;height:46px;background:var(--yellow)}
.main-nav a{position:absolute;top:0;height:46px;display:flex;align-items:center;justify-content:center;font-family:"Montserrat",sans-serif;font-weight:600;font-size:13px;color:var(--ink);text-decoration:none;letter-spacing:.5px;transform:translateX(-50%);white-space:nowrap}
.main-nav a.active{background:var(--green);color:var(--white);width:134px}

/* hero */
.hero{top:180px;height:621px;background:
  radial-gradient(ellipse 320px 380px at 330px 260px,rgba(214,166,132,.75),rgba(214,166,132,0) 70%),
  radial-gradient(ellipse 260px 320px at 720px 260px,rgba(226,214,150,.6),rgba(226,214,150,0) 70%),
  linear-gradient(100deg,#e6e3df 0%,#bdb2a8 30%,#8c8478 55%,#5a5a58 78%,#3f4a42 100%)}
.hero-caption{left:711px;top:182px;width:489px;height:261px;background:rgba(40,40,40,.72);display:flex;align-items:center;justify-content:flex-end;padding-right:45px}
.hero-caption h1{font-family:"Montserrat",sans-serif;font-weight:700;font-size:36px;line-height:56px;color:var(--white);text-align:right;letter-spacing:1px}
.dots{left:556px;top:556px;display:flex;gap:10px}
.dots span{width:11px;height:11px;border-radius:50%;background:rgba(255,255,255,.6)}
.dots span:first-child{background:var(--white)}

/* welcome */
.welcome{top:801px;height:224px;background:var(--yellow);text-align:center}
.welcome h2{position:absolute;top:36px;width:100%;font-family:"Montserrat",sans-serif;font-weight:400;font-size:28px;color:var(--green)}
.welcome h2 b{font-weight:700}
.welcome p{position:absolute;left:80px;top:84px;width:1040px;font-size:13.5px;line-height:21px;color:var(--ink)}
.pill{display:flex;align-items:center;justify-content:center;background:var(--green);color:var(--white);font-family:"Montserrat",sans-serif;font-weight:700;font-size:11px;border-radius:14px;border:2px solid var(--white);white-space:nowrap}
.welcome .pill{position:absolute;left:549px;top:160px;width:102px;height:28px}

/* section headings */
.sec-title{position:absolute;width:100%;text-align:center;font-family:"Montserrat",sans-serif;font-size:28px;font-weight:400;color:var(--white);letter-spacing:.5px}
.sec-title b{font-weight:700}
.rule{position:absolute;left:560px;width:80px;height:3px;background:var(--yellow)}
.sec-sub{position:absolute;width:100%;text-align:center;font-family:"Montserrat",sans-serif;font-size:15px;color:var(--white)}

/* services */
.services{top:1025px;height:436px;background:
  radial-gradient(ellipse 300px 200px at 250px 330px,rgba(150,140,130,.45),rgba(150,140,130,0) 70%),
  radial-gradient(ellipse 320px 220px at 950px 300px,rgba(140,130,125,.45),rgba(140,130,125,0) 70%),
  linear-gradient(180deg,#707072,#59595b 60%,#4f4f51)}
.service{position:absolute;top:210px;width:240px;text-align:center;transform:translateX(-50%)}
.service-icon{width:116px;height:116px;margin:0 auto;border-radius:50%;background:var(--white);padding:5px}
.service-icon div{width:100%;height:100%;border-radius:50%;background:radial-gradient(circle at 40% 35%,var(--green-light),var(--green) 55%,var(--green-dark))}
.service h3{margin-top:22px;font-family:"Montserrat",sans-serif;font-size:13.5px;font-weight:700;color:var(--white);white-space:nowrap}

/* gallery */
.gallery{top:1461px;height:508px;background:var(--green)}
.shot{position:absolute}
.video-player{left:81px;top:145px;width:309px;height:310px;background:
  radial-gradient(ellipse 110px 140px at 200px 120px,rgba(60,50,45,.7),rgba(60,50,45,0) 70%),
  linear-gradient(180deg,#e4e4e4 0%,#bcbcbc 45%,#6a6a6a 80%,#3a3a3a)}
.video-bar{position:absolute;left:0;bottom:0;width:100%;height:36px;background:rgba(0,0,0,.75);display:flex;align-items:center;padding:0 14px;gap:14px}
.video-track{flex:1;height:5px;background:#555;border-radius:3px;position:relative}
.video-track i{position:absolute;left:0;top:0;height:5px;width:55%;background:#2f8de4;border-radius:3px}
.arrow{position:absolute}

/* events */
.events{top:1969px;height:547px;background:
  radial-gradient(ellipse 300px 180px at 600px 120px,rgba(150,150,150,.35),rgba(150,150,150,0) 70%),
  linear-gradient(180deg,#6d6d6f,#58585a)}
.event-card{position:absolute;top:177px;width:327px;height:305px;background:var(--white);border-radius:3px;text-align:center}
.event-photo{height:174px;border-radius:3px 3px 0 0}
.event-date{position:absolute;left:8px;top:0;width:44px;height:56px;background:var(--green);color:var(--white);font-family:"Montserrat",sans-serif;text-align:center}
.event-date b{display:block;font-size:20px;line-height:32px}
.event-date span{display:block;font-size:11px;font-weight:600}
.event-card h4{margin-top:16px;font-family:"Montserrat",sans-serif;font-weight:700;font-size:13px;color:var(--ink)}
.event-card p{margin:8px auto 0;width:270px;font-size:11.5px;line-height:16px;color:#444}
.event-card .pill{position:absolute;left:114px;bottom:-12px;width:100px;height:28px;font-size:10px}

/* testimonials */
.testimonials{top:2516px;height:438px;background:var(--black)}
.quote-box{left:166px;top:161px;width:868px;height:153px;background:var(--green);border-radius:4px;padding:22px 36px 0 60px;font-size:13px;line-height:21px;color:var(--white);font-weight:600}
.quote-tail{left:240px;top:312px}
.quote-name{left:288px;top:343px;font-family:"Montserrat",sans-serif;font-weight:700;font-size:18px;color:var(--white);letter-spacing:.5px}

/* footer */
.site-footer{top:2954px;height:457px;background:var(--footer);color:var(--white)}
.newsletter{left:81px;top:53px;width:757px;height:67px;border:1px solid #555;display:flex;align-items:center;padding-left:14px;gap:10px}
.newsletter svg{flex-shrink:0}
.newsletter h5{font-family:"Montserrat",sans-serif;font-size:16px;font-weight:700;white-space:nowrap;flex-shrink:0}
.news-input{width:380px;height:40px;background:var(--white);color:#333;font-size:12px;display:flex;align-items:center;padding-left:10px;margin-left:14px;flex-shrink:0}
.news-btn{width:99px;height:40px;background:var(--green);font-family:"Montserrat",sans-serif;font-size:12px;font-weight:700;display:flex;align-items:center;justify-content:center;margin-left:-10px;flex-shrink:0}
.follow{left:889px;top:72px;display:flex;align-items:center;gap:12px;font-family:"Montserrat",sans-serif;font-weight:700;font-size:16px;white-space:nowrap}
.col-title{position:absolute;display:flex;align-items:center;gap:10px;font-family:"Montserrat",sans-serif;font-size:16px;font-weight:700;white-space:nowrap}
.field{position:absolute;border:1px solid #bbb;color:#ddd;font-size:12px;padding:10px 10px}
.submit{position:absolute;left:323px;top:349px;width:226px;height:37px;background:var(--green);font-family:"Montserrat",sans-serif;font-size:12px;font-weight:700;display:flex;align-items:center;justify-content:center}
.vline{position:absolute;top:170px;width:1px;height:236px;background:#555}
.links{position:absolute;left:644px;top:216px;list-style:none;font-family:"Montserrat",sans-serif;font-size:12px;line-height:29px;color:#ddd}
.links li::before{content:"›";margin-right:8px}
.contact-line{position:absolute;left:866px;display:flex;align-items:center;gap:12px;font-family:"Montserrat",sans-serif;font-weight:600;white-space:nowrap}
.footer-brand{left:866px;top:330px;display:flex;align-items:center;gap:10px}
.footer-brand .brand-name{font-size:26px;color:var(--yellow)}
.footer-brand .brand-dot{background:var(--yellow);width:20px;height:20px}
.copyright{top:3411px;height:51px;background:var(--black);border-top:5px solid var(--yellow);text-align:center;font-family:"Montserrat",sans-serif;font-size:12px;color:#ccc;line-height:46px}
.copyright-notch{left:578px;top:-5px}
</style>
</head>
<body>

<header class="site-header">
  <div class="abs brand"><span class="brand-dot"></span><span class="brand-name">VORELAN</span></div>
  <div class="abs join-btn">Join A Session</div>
  <div class="abs header-contact">
    <span class="round-icon"><svg width="16" height="16" viewBox="0 0 24 24"><path fill="#fff" d="M6.6 10.8a15.2 15.2 0 0 0 6.6 6.6l2.2-2.2c.3-.3.7-.4 1-.2 1.1.4 2.3.6 3.6.6.6 0 1 .4 1 1V20c0 .6-.4 1-1 1A17 17 0 0 1 3 4c0-.6.4-1 1-1h3.5c.6 0 1 .4 1 1 0 1.3.2 2.5.6 3.6.1.3 0 .7-.2 1z"/></svg></span>
    123-345-5678
    <span class="social" style="background:#2f4f94;margin-left:6px"></span>
    <span class="social" style="background:#8a8a8a"></span>
  </div>
</header>

<nav class="main-nav">
  <a class="active" style="left:148px">HOME</a>
  <a style="left:284px">ABOUT</a>
  <a style="left:432px">SERVICES</a>
  <a style="left:572px">BLOG</a>
  <a style="left:711px">VIDEOS</a>
  <a style="left:870px">PROGRAMS</a>
  <a style="left:1036px">CONTACT</a>
</nav>

<section class="hero" role="img" aria-label="Athletes training together on suspension straps in a bright gym">
  <div class="abs hero-caption"><h1>WHERE PERSONAL<br>TRAINING MEETS<br>GROUP TRAINING</h1></div>
  <div class="abs dots"><span></span><span></span><span></span></div>
</section>

<section class="welcome">
  <h2>WELCOME TO <b>VORELAN</b></h2>
  <p>Lorem ipsum dolor sit amet, consectetuer adipiscing elit, sed diam nonummy nibh euismod tincidunt ut laoreet dolore magna aliquam erat volutpat. Ut wisi enim ad minim veniam, quis nostrud exerci tation ullamcorper suscipit lobortis nisl ut aliquip ex ea commodo consequat. Duis autem vel eum iriure dolor in hendrerit in vulputate velit esse molestie consequat, vel illum dolore eu feugiat nulla facilisis.</p>
  <div class="pill">READ MORE</div>
</section>

<section class="services" role="region" aria-label="Services over a photo of a stretching class">
  <h2 class="sec-title" style="top:56px">OUR <b>SERVICES</b></h2>
  <div class="rule" style="top:112px"></div>
  <div class="sec-sub" style="top:143px">SELECT TO LEARN MORE!</div>
  <div class="service" style="left:183px"><div class="service-icon"><div role="img" aria-label="Personal training pictogram"></div></div><h3>PERSONAL TRAINING</h3></div>
  <div class="service" style="left:461px"><div class="service-icon"><div role="img" aria-label="Bootcamp class pictogram"></div></div><h3>OUTDOOR BOOTCAMP CLASSES</h3></div>
  <div class="service" style="left:738px"><div class="service-icon"><div role="img" aria-label="Group runners pictogram"></div></div><h3>OUTDOOR GROUP TRAINING</h3></div>
  <div class="service" style="left:1012px"><div class="service-icon"><div role="img" aria-label="Online coaching pictogram"></div></div><h3>ONLINE COACHING</h3></div>
</section>

<section class="gallery">
  <h2 class="sec-title" style="top:50px">OUR <b>GALLERY</b></h2>
  <div class="rule" style="top:106px"></div>
  <svg class="arrow" style="left:28px;top:272px" width="20" height="36" viewBox="0 0 20 36"><path d="M18 2 3 18l15 16" fill="none" stroke="#fff" stroke-width="2"/></svg>
  <svg class="arrow" style="left:1152px;top:272px" width="20" height="36" viewBox="0 0 20 36"><path d="M2 2l15 16L2 34" fill="none" stroke="#fff" stroke-width="2"/></svg>
  <div class="shot video-player" role="img" aria-label="Training video of a trainer coaching a kettlebell push-up">
    <div class="video-bar">
      <svg width="12" height="14" viewBox="0 0 12 14"><path d="M0 0l12 7-12 7z" fill="#fff"/></svg>
      <svg width="16" height="14" viewBox="0 0 16 14"><path d="M0 4h4l5-4v14l-5-4H0z" fill="#fff"/></svg>
      <div class="video-track"><i></i></div>
    </div>
  </div>
  <div class="shot" style="left:404px;top:145px;width:196px;height:148px;background:linear-gradient(180deg,#5a5a5a 0%,#8e8278 45%,#b9a898 70%,#2e2e2e 100%)" role="img" aria-label="Man doing dumbbell rows"></div>
  <div class="shot" style="left:404px;top:309px;width:196px;height:146px;background:linear-gradient(180deg,#f1f4ee 0%,#d6e2cc 40%,#9cc06f 70%,#6e9a44 100%)" role="img" aria-label="Group doing push-ups on grass"></div>
  <div class="shot" style="left:614px;top:145px;width:288px;height:148px;background:linear-gradient(180deg,#fafafa 0%,#ece6e0 40%,#c3a58e 70%,#3b3b3b 100%)" role="img" aria-label="Class doing plank exercises"></div>
  <div class="shot" style="left:614px;top:309px;width:148px;height:146px;background:linear-gradient(180deg,#d8d3cf 0%,#c98f86 45%,#b2343f 70%,#2c2c2c 100%)" role="img" aria-label="Woman stretching on a mat"></div>
  <div class="shot" style="left:776px;top:309px;width:126px;height:146px;background:linear-gradient(180deg,#d0a23a 0%,#6f8a78 40%,#3c6e9c 70%,#262b2f 100%)" role="img" aria-label="Balance ball workout"></div>
  <div class="shot" style="left:916px;top:145px;width:204px;height:310px;background:linear-gradient(180deg,#2a2a2a 0%,#8a6d5a 35%,#c79c7e 55%,#4a3e36 80%,#1e1e1e 100%)" role="img" aria-label="Man lifting dumbbells with a trainer"></div>
</section>

<section class="events">
  <h2 class="sec-title" style="top:55px">UPCOMING <b>EVENTS</b></h2>
  <div class="rule" style="top:112px"></div>
  <div class="sec-sub" style="top:127px">JOIN US FOR AN EVENT!</div>
  <svg class="arrow" style="left:28px;top:312px" width="20" height="36" viewBox="0 0 20 36"><path d="M18 2 3 18l15 16" fill="none" stroke="#fff" stroke-width="2"/></svg>
  <svg class="arrow" style="left:1152px;top:312px" width="20" height="36" viewBox="0 0 20 36"><path d="M2 2l15 16L2 34" fill="none" stroke="#fff" stroke-width="2"/></svg>

  <article class="event-card" style="left:81px">
    <div class="event-photo" role="img" aria-label="Outdoor group exercise class in a park" style="background:linear-gradient(180deg,#3f6a2a 0%,#8fb868 30%,#d7c9c0 55%,#7fb04f 80%,#4f8a2e 100%)"></div>
    <div class="event-date"><b>12</b><span>MAY</span></div>
    <h4>LOREM IPSUM DOLOR SIT AMET</h4>
    <p>Lorem ipsum dolor sit amet, consectetuer adipiscie elit, sed di nonummy nibh euismod tincidun euismod...</p>
    <div class="pill">READ MORE</div>
  </article>
  <article class="event-card" style="left:436px">
    <div class="event-photo" role="img" aria-label="Indoor gym workout session" style="background:linear-gradient(180deg,#f4f4f4 0%,#dcdcdc 35%,#d49a8a 60%,#8e8e8e 85%,#5c5c5c 100%)"></div>
    <div class="event-date"><b>11</b><span>MAY</span></div>
    <h4>LOREM IPSUM DOLOR SIT AMET</h4>
    <p>Lorem ipsum dolor sit amet, consectetuer adipiscie elit, sed di nonummy nibh euismod tincidun euismod...</p>
    <div class="pill">READ MORE</div>
  </article>
  <article class="event-card" style="left:792px">
    <div class="event-photo" role="img" aria-label="Suspension strap training outdoors with a coach" style="background:linear-gradient(180deg,#9cc978 0%,#6ea84a 35%,#5a86c0 65%,#3c6fa8 100%)"></div>
    <div class="event-date"><b>09</b><span>MAY</span></div>
    <h4>LOREM IPSUM DOLOR SIT AMET</h4>
    <p>Lorem ipsum dolor sit amet, consectetuer adipiscie elit, sed di nonummy nibh euismod tincidun euismod...</p>
    <div class="pill">READ MORE</div>
  </article>
</section>

<section class="testimonials">
  <h2 class="sec-title" style="top:50px">CLIENT <b>TESTIMONIALS</b></h2>
  <div class="rule" style="top:106px"></div>
  <svg class="arrow" style="left:28px;top:234px" width="20" height="36" viewBox="0 0 20 36"><path d="M18 2 3 18l15 16" fill="none" stroke="#fff" stroke-width="2"/></svg>
  <svg class="arrow" style="left:1152px;top:234px" width="20" height="36" viewBox="0 0 20 36"><path d="M2 2l15 16L2 34" fill="none" stroke="#fff" stroke-width="2"/></svg>
  <div class="abs quote-box">
    <svg class="abs" style="left:22px;top:20px" width="26" height="20" viewBox="0 0 26 20"><path d="M0 20V10C0 4 3 0 10 0v4c-3 0-5 2-5 6h5v10zm14 0V10c0-6 3-10 10-10v4c-3 0-5 2-5 6h5v10z" fill="#2f9a5c"/></svg>
    Ut wisi enim adi minim veniam, quis nostrudk exerci tation more ullamcorper suscipit lobortis nis ut aliquip commodo conseqti. Duis auteem iriure dolor in hendrerit in vulputate veesseml molestie consequat, vel illum facilisi. Lorem ipsum dolor sit amet, conse ctetuer adipiscing elit, sedmoi di nonummy nibh more euismod tincidunt ut laoreet dolore magna aliquam erat volutpat. Ut wisi enim admin veniam, quis nostrud exerci tation ullamco orper suscipit lobortis eamopk commodo consequat.
  </div>
  <svg class="abs quote-tail" width="40" height="28" viewBox="0 0 40 28"><path d="M0 0h40L10 28z" fill="var(--green)"/></svg>
  <div class="abs quote-name">DANE HOLLOWAY</div>
</section>

<footer class="site-footer">
  <div class="abs newsletter">
    <svg width="24" height="24" viewBox="0 0 24 24"><circle cx="12" cy="12" r="11" fill="#555"/><path d="M6 8h12v8H6zM6 8l6 5 6-5" fill="none" stroke="#ddd" stroke-width="1.5"/></svg>
    <h5>NEWSLETTER SIGNUP</h5>
    <div class="news-input">Enter your email here</div>
    <div class="news-btn">SUBSCRIBE</div>
  </div>
  <div class="abs follow">FOLLOW US
    <span class="social" style="background:#2f4f94"></span>
    <span class="social" style="background:#8a8a8a"></span>
  </div>

  <div class="col-title" style="left:81px;top:164px"><svg width="26" height="26" viewBox="0 0 26 26"><circle cx="13" cy="13" r="12" fill="none" stroke="#888" stroke-width="2"/><text x="13" y="18" text-anchor="middle" font-size="14" fill="#888" font-family="Montserrat,sans-serif">?</text></svg>QUICK INQUIRY</div>
  <div class="field" style="left:81px;top:233px;width:226px;height:37px">Name</div>
  <div class="field" style="left:81px;top:291px;width:226px;height:37px">Email Address</div>
  <div class="field" style="left:81px;top:349px;width:226px;height:37px">Phone Number</div>
  <div class="field" style="left:323px;top:233px;width:231px;height:93px">Message</div>
  <div class="submit">SUBMIT</div>

  <div class="vline" style="left:600px"></div>
  <div class="col-title" style="left:628px;top:170px"><svg width="20" height="22" viewBox="0 0 20 22"><rect x="1" y="1" width="18" height="20" fill="none" stroke="#888" stroke-width="2"/><path d="M5 7h10M5 11h10M5 15h10" stroke="#888" stroke-width="2"/></svg>QUICK LINKS</div>
  <ul class="links"><li>HOME</li><li>ABOUT</li><li>SERVICES</li><li>BLOG</li><li>VIDEOS</li><li>PROGRAMS</li><li>CONTACT</li></ul>

  <div class="vline" style="left:836px"></div>
  <div class="col-title" style="left:866px;top:170px"><svg width="24" height="24" viewBox="0 0 24 24"><circle cx="12" cy="12" r="11" fill="#555"/><circle cx="12" cy="10" r="4" fill="#ccc"/></svg>CONTACT DETAILS</div>
  <div class="contact-line" style="top:228px;font-size:18px"><span class="round-icon"><svg width="16" height="16" viewBox="0 0 24 24"><path fill="#fff" d="M6.6 10.8a15.2 15.2 0 0 0 6.6 6.6l2.2-2.2c.3-.3.7-.4 1-.2 1.1.4 2.3.6 3.6.6.6 0 1 .4 1 1V20c0 .6-.4 1-1 1A17 17 0 0 1 3 4c0-.6.4-1 1-1h3.5c.6 0 1 .4 1 1 0 1.3.2 2.5.6 3.6.1.3 0 .7-.2 1z"/></svg></span>123-456-7890</div>
  <div class="contact-line" style="top:278px;font-size:13px"><span class="round-icon"><svg width="16" height="12" viewBox="0 0 16 12"><path d="M1 1h14v10H1zM1 1l7 5 7-5" fill="none" stroke="#fff" stroke-width="1.5"/></svg></span>info@vorelan.com</div>
  <div class="abs footer-brand"><span class="brand-dot"></span><span class="brand-name">VORELAN</span></div>
</footer>

<section class="copyright">
  <svg class="abs copyright-notch" width="44" height="16" viewBox="0 0 44 16"><path d="M0 0h44L22 16z" fill="var(--yellow)"/></svg>
  COPYRIGHT 2016 VORELAN &nbsp;|&nbsp; ALL RIGHT RESERVED.
</section>

</body>
</html>
```